Tobias Ränkel and Co stationary design

Name of business:
Tobias Ränkel and Co

Can be written as:
Tobias Ränkel and Co
Tobias Ränkel & Co
tobias ränkel & co

If broken into letters:
TR&Co
tr&co

We are a Railway Safety Training Company
Our focus is on rail safety, Rail Management, Safety Management, Train Control Training, Accident Investigation.

.

Project Deadline Extended Reason: The original date was set to commence as soon as the logo contest finished. Sketch harbor started the project as soon as it was paid. Added Thursday, May 12, 2016

Target Market(s)

Professionals, CEO's and Managing Directors

Industry/Entity Type

Management Consulting

Font styles to use
Sans Serif

Requirements
Must have
• Professional, Sharp, Creative and modern
• Please note that this is for stationary concept which must include
• - business card
• - letterhead
• - envelope
• - with compliments slip
• - document cover (like book or folder cover)
• - dividers for folders....
• These must all have a common theme or style
Nice to have
• Keep if fresh
Should not have
• Please don't sent just fonts.... Must be creative

```html
<!DOCTYPE html>
<html lang="en">
<head>
<meta charset="utf-8">
<title>Tobias Ränkel &amp; Co – Business Card</title>
<link rel="stylesheet" href="https://fonts.googleapis.com/css2?family=Exo+2:ital,wght@0,400;0,600;1,700&family=Open+Sans:wght@400;600&display=swap">
<style>
  :root {
    --navy: #1f3a74;
    --navy-light: #2f4f92;
    --red: #c8102e;
    --white: #ffffff;
    --paper: #f7f7f8;
    --paper-shade: #e4e5e8;
    --ink: #3c4250;
    --ink-soft: #5d6370;
    --backdrop: #e9e9ec;
  }
  * { margin: 0; padding: 0; box-sizing: border-box; }
  html, body { width: 1200px; height: 843px; overflow: hidden; }
  body {
    background: var(--backdrop);
    font-family: "Open Sans", sans-serif;
    position: relative;
  }
  .card {
    position: absolute;
    left: 285px;
    width: 630px;
    height: 360px;
    overflow: hidden;
    box-shadow: 0 6px 18px rgba(0,0,0,0.18);
  }

  /* Back of card */
  .card-back {
    top: 40px;
    background: linear-gradient(135deg, var(--navy-light) 0%, var(--navy) 60%, #1a3266 100%);
  }
  .card-back .brand-name {
    position: absolute;
    left: 44px; top: 58px;
    font-family: "Exo 2", sans-serif;
    font-style: italic;
    font-weight: 700;
    font-size: 26px;
    color: var(--white);
  }
  .card-back .brand-web {
    position: absolute;
    left: 46px; top: 96px;
    font-size: 13px;
    letter-spacing: 6px;
    color: var(--white);
  }
  .card-back .brand-circle {
    position: absolute;
    right: -60px; top: -40px;
  }

  /* Front of card */
  .card-front {
    top: 443px;
    background: linear-gradient(160deg, var(--white) 0%, var(--paper) 55%, var(--paper-shade) 100%);
  }
  .name-band {
    position: absolute;
    left: 0; top: 62px;
    width: 78%; height: 86px;
    background: linear-gradient(90deg, var(--navy) 0%, var(--navy-light) 50%, var(--navy) 100%);
  }
  .accent-band {
    position: absolute;
    right: 0; top: 62px;
    width: 22%; height: 100px;
    background: var(--red);
  }
  .person-name {
    position: absolute;
    left: 52px; top: 76px;
    font-size: 20px;
    font-weight: 600;
    letter-spacing: 0.5px;
    color: var(--white);
  }
  .person-role {
    position: absolute;
    left: 52px; top: 103px;
    font-size: 14px;
    color: var(--white);
  }
  .brand-mark {
    position: absolute;
    left: 432px; top: 66px;
  }
  .brand-lockup {
    position: absolute;
    right: 58px; top: 164px;
    font-family: "Exo 2", sans-serif;
    font-style: italic;
    font-weight: 700;
    font-size: 20px;
    color: var(--navy);
  }
  .contact-list {
    position: absolute;
    left: 52px; top: 192px;
    list-style: none;
  }
  .contact-list li {
    display: flex;
    align-items: center;
    gap: 10px;
    font-size: 15px;
    line-height: 23px;
    color: var(--ink);
  }
  .contact-list li.email { color: var(--ink-soft); font-size: 16px; }
  .contact-list svg { width: 14px; height: 14px; fill: var(--navy); flex: none; }
  .address {
    position: absolute;
    right: 52px; top: 262px;
    text-align: right;
    font-size: 15px;
    line-height: 21px;
    color: var(--ink-soft);
  }
  .address .web { letter-spacing: 2.5px; font-size: 16px; }
</style>
</head>
<body>

  <section class="card card-back" aria-label="Business card, back">
    <p class="brand-name">Tobias Ränkel &amp; Co.</p>
    <p class="brand-web">www.sitename.com</p>
    <svg class="brand-circle" width="340" height="340" viewBox="0 0 340 340" aria-hidden="true">
      <circle cx="170" cy="170" r="150" fill="none" stroke="rgba(255,255,255,0.9)" stroke-width="14"/>
    </svg>
  </section>

  <section class="card card-front" aria-label="Business card, front">
    <div class="name-band"></div>
    <div class="accent-band"></div>
    <p class="person-name">MARTIN HALE</p>
    <p class="person-role">CEO/FOUNDER</p>

    <svg class="brand-mark" width="98" height="98" viewBox="0 0 98 98" aria-hidden="true">
      <circle cx="49" cy="49" r="44" fill="var(--white)" stroke="var(--navy)" stroke-width="6"/>
    </svg>
    <p class="brand-lockup">Tobias Ränkel &amp; Co.</p>

    <ul class="contact-list">
      <li>
        <svg viewBox="0 0 24 24"><path d="M6.6 10.8a15.1 15.1 0 0 0 6.6 6.6l2.2-2.2a1 1 0 0 1 1-.25 11.4 11.4 0 0 0 3.6.57 1 1 0 0 1 1 1V20a1 1 0 0 1-1 1A17 17 0 0 1 3 4a1 1 0 0 1 1-1h3.5a1 1 0 0 1 1 1c0 1.25.2 2.45.57 3.57a1 1 0 0 1-.25 1z"/></svg>
        614 502 7731
      </li>
      <li>
        <svg viewBox="0 0 24 24"><path d="M7 1h10a2 2 0 0 1 2 2v18a2 2 0 0 1-2 2H7a2 2 0 0 1-2-2V3a2 2 0 0 1 2-2zm0 3v14h10V4zm5 15.2a1.2 1.2 0 1 0 0 2.4 1.2 1.2 0 0 0 0-2.4z"/></svg>
        729 815 3046
      </li>
      <li>
        <svg viewBox="0 0 24 24"><path d="M6 2h9l3 3v4H6zM3 10h18a1 1 0 0 1 1 1v8a1 1 0 0 1-1 1h-2v2H5v-2H3a1 1 0 0 1-1-1v-8a1 1 0 0 1 1-1zm4 6v4h10v-4z"/></svg>
        358 260 4817
      </li>
      <li class="email">
        <svg viewBox="0 0 24 24"><path d="M2 5h20v14H2zm2 2v.5l8 5 8-5V7zm0 3v7h16v-7l-8 5z"/></svg>
        mail@sitename.com
      </li>
    </ul>

    <address class="address">
      4120 Juniper Court<br>
      Fairbanks, Alaska 37218<br>
      <span class="web">www.sitename.com</span>
    </address>
  </section>

</body>
</html>
```